"Inkvale" printing shop

-The design must be based around the attached HPID (home page information design) called "Inkvale - HPID".

The table boxes are just for approximate placement of information – you DON'T have to box everything in and you can arrange these. All fonts used in the HPID are only examples - you can use any Google font you wish.

- Information only is in orange text. Copy to go on the design in black text. Some instructions are in the HPID. Please be creative!

-The design needs to be modern. Colours are to be consistent with their new logo or complement it. Keep it clean and simple, you don't need to use lots of colours. Use lots of white.

- images / icons for the site need to be relevant and high quality, but they must also be free images or icons. I have attached a few examples that could be used.

Width of content will be 1100 pixels when implemented as a web page. Header height (without nav bar) 150-200 pixels.

If your design is chosen the winning PSD file will have to be provided as follows…
1. Canvas size of 2000px x 2000px - 72ppi in Adobe Photoshop (CS5 compatible)
2. Width of content section is 1100px wide - centered in the canvas
3. Any button rollovers/hovers in the PSD as hidden layers.
4. All fonts used must be Google fonts.
5. You will need to supply the chosen home page plus one example page (example page as a style guide for how all other pages will look). Example page is only the header and navigational bar at the top, an empty sector in the middle with a column (190 px wide) which can be left or right aligned which means the main sector is 910 pixels wide, and then the footer at the bottom of the page

Checklist - http://pagebuildertally.example/

Examples of some websites that have great design... don't copy them please but they are similar in look to what we are after....
http://www.rookfenly.example/

Industry/Entity Type

Printing

Font styles to use
Serif
Sans Serif

Requirements
Should not have
• Drop shadows, comic sans font

```html
<!DOCTYPE html>
<html lang="en">
<head>
<meta charset="utf-8">
<title>Inkvale Printing Shop</title>
<link rel="stylesheet" href="https://fonts.googleapis.com/css2?family=Lato:ital,wght@0,300;0,400;0,700;1,400;1,700&family=Lora:ital@1&display=swap">
<style>
:root{
  --pink:#fd78ab;
  --white:#ffffff;
  --page:#fbfbfb;
  --panel:#f5f5f5;
  --ink:#333333;
  --fold:#d6d6d6;
  --field:#f4a3c2;
}
*{box-sizing:border-box;margin:0;padding:0}
html,body{width:760px;height:1200px;overflow:hidden}
body{position:relative;background:var(--page);font-family:'Lato',Arial,sans-serif;color:var(--ink)}
.abs{position:absolute}
.top-nav{top:6px;right:78px;font-size:7.5px;color:var(--pink);word-spacing:1px}
.top-nav span{margin:0 7px;color:var(--pink)}
.brand{left:78px;top:25px;display:flex;align-items:center;gap:5px;white-space:nowrap}
.brand-dot{width:24px;height:24px;border-radius:50%;background:var(--pink)}
.brand-name{font-size:16px;font-weight:700;color:var(--pink)}
.tagline{left:177px;top:20px;font-size:18.5px;letter-spacing:2.4px;font-weight:400;color:#222;white-space:nowrap}
.subline{left:177px;top:48px;font-size:7.2px;font-style:italic;font-weight:700;letter-spacing:.6px;color:#222;white-space:nowrap}
.contact{left:592px;top:32px;font-size:7.3px;color:var(--pink);line-height:8.5px}
.contact div{display:flex;gap:6px;margin-bottom:6px}
.service-nav{left:78px;top:98px;width:604px;font-size:7.6px;color:var(--pink);display:flex;justify-content:space-between}
.service-nav i{font-style:normal;color:var(--pink)}
.hero{left:0;top:120px;width:760px;height:284px;background:var(--pink)}
.hero-title{left:78px;top:76px;font-family:'Lora',Georgia,serif;font-style:italic;font-weight:400;font-size:22.5px;line-height:28px;color:var(--white);letter-spacing:.6px}
.btn{background:var(--white);color:var(--pink);font-weight:700;border-radius:3px;display:flex;align-items:center;justify-content:center;gap:5px}
.hero-btn{left:78px;top:178px;width:87px;height:26px;font-size:8.5px}
.hero-art{left:408px;top:27px;width:255px;height:229px;border-radius:3px;background:linear-gradient(180deg,#cfd2d6 0%,#f2f2f2 20%,#f7c62a 45%,#f4f4f4 80%,#e9e9e9 100%)}
.arrow{top:115px;width:20px;height:20px;border-radius:50%;background:var(--white);display:flex;align-items:center;justify-content:center}
.card{width:190px;height:198px;background:var(--pink);color:var(--white);text-align:center;overflow:hidden}
.card .fold{position:absolute;left:0;top:0}
.card .icon{position:absolute;left:75px;top:22px}
.card h3{position:absolute;left:0;right:0;top:63px;font-weight:300;font-size:15.5px}
.card h3 span{border-bottom:1px solid var(--white);padding-bottom:1px}
.card h4{position:absolute;left:0;right:0;top:95px;font-size:9.7px;font-weight:700}
.card p{position:absolute;left:12px;right:12px;top:117px;font-size:6.9px;line-height:8.4px}
.card .btn{position:absolute;left:60px;top:161px;width:71px;height:20px;font-size:7.6px}
.quote{left:0;top:868px;width:760px;height:239px;background:var(--panel)}
.quote h2{font-weight:400;font-size:14px;color:#333}
.quote-text{left:78px;top:57px;width:250px;font-size:9.6px;line-height:13px}
.socials{left:78px;top:182px;display:flex;gap:13px}
.socials div{width:30px;height:30px;border-radius:50%;background:var(--pink)}
.field{border:1px solid var(--field);background:var(--white);font-size:7.5px;color:#999;padding:7px 6px}
.submit{left:388px;top:191px;width:71px;height:19px;background:var(--pink);color:var(--white);font-size:7.6px;font-weight:700;border-radius:3px;display:flex;align-items:center;justify-content:center}
.footer{left:0;top:1107px;width:760px;height:40px;background:var(--pink);color:var(--white);font-size:6.4px;display:flex;align-items:center;justify-content:center;gap:3px}
.copyright{left:0;top:1168px;width:760px;text-align:center;font-size:7.5px;color:var(--pink)}
</style>
</head>
<body>
<nav class="abs top-nav">Home<span>|</span>About<span>|</span>Free Quote<span>|</span>Contact</nav>
<div class="abs brand"><div class="brand-dot"></div><div class="brand-name">Inkvale</div></div>
<div class="abs tagline">Duplication is our vocation</div>
<div class="abs subline">Professional photocopying - digital &amp; film processing, design and printing</div>
<div class="abs contact">
  <div><svg width="8" height="8" viewBox="0 0 10 10"><path d="M2 0.5 L4 2.8 L3 4 Q4.2 6 6 7 L7.2 6 L9.5 8 L8 9.6 Q3.5 9 0.4 2 Z" fill="var(--pink)"/></svg>07 555 0190,</div>
  <div><svg width="8" height="10" viewBox="0 0 8 10"><path d="M4 0 A4 4 0 0 1 8 4 C8 6.5 4 10 4 10 C4 10 0 6.5 0 4 A4 4 0 0 1 4 0Z" fill="var(--pink)"/><circle cx="4" cy="4" r="1.5" fill="var(--page)"/></svg><span>12/48 Harbour Lane<br>Kelmount - Bayhaven</span></div>
</div>
<nav class="abs service-nav"><span>Photocopying</span><i>|</i><span>Printing</span><i>|</i><span>Laminating</span><i>|</i><span>Business cards</span><i>|</i><span>Typing Services</span><i>|</i><span>Film Processing</span><i>|</i><span>Photo Printing</span><i>|</i><span>Passport Photos</span><i>|</i><span>Image Restoration</span><i>|</i><span>Printer Supplies</span></nav>

<section class="abs hero">
  <div class="abs arrow" style="left:16px"><svg width="8" height="8" viewBox="0 0 8 8"><path d="M5.5 1 L2.5 4 L5.5 7" stroke="var(--pink)" stroke-width="1.8" fill="none"/></svg></div>
  <div class="abs arrow" style="left:724px"><svg width="8" height="8" viewBox="0 0 8 8"><path d="M2.5 1 L5.5 4 L2.5 7" stroke="var(--pink)" stroke-width="1.8" fill="none"/></svg></div>
  <h1 class="abs hero-title">Digital Printing Laminating<br>Photocopying Services<br>Throughout Bayhaven</h1>
  <div class="abs btn hero-btn">LEARN MORE <svg width="6" height="8" viewBox="0 0 6 8"><path d="M1 1 L4.5 4 L1 7" stroke="var(--pink)" stroke-width="1.8" fill="none"/></svg></div>
  <div class="abs hero-art" role="img" aria-label="Large format printer rollers feeding out a printed sunflower photo with colour calibration bars"></div>
</section>

<svg width="0" height="0" style="position:absolute">
  <defs>
    <g id="fold"><path d="M0 0 H52 Q40 8 50 18 Q28 40 0 66 Z" fill="var(--fold)"/></g>
  </defs>
</svg>

<article class="abs card" style="left:78px;top:431px">
  <svg class="fold" width="60" height="70"><use href="#fold"/></svg>
  <svg class="icon" width="40" height="40" viewBox="0 0 40 40"><circle cx="20" cy="20" r="19" fill="var(--white)"/><path d="M8 17 L20 11 L32 17 L20 23 Z" fill="var(--pink)"/><path d="M8 21 L20 27 L32 21" stroke="var(--pink)" stroke-width="2.2" fill="none"/><path d="M8 25 L20 31 L32 25" stroke="var(--pink)" stroke-width="2.2" fill="none"/></svg>
  <h3><span>Photocopying</span></h3>
  <h4>Cost effective photocopying</h4>
  <p>No matter the quantity of photocopies you need or the size of your copy - you can rely on us to provide a top quality service!</p>
  <div class="btn">READ MORE <svg width="6" height="8" viewBox="0 0 6 8"><path d="M1 1 L4.5 4 L1 7" stroke="var(--pink)" stroke-width="1.8" fill="none"/></svg></div>
</article>

<article class="abs card" style="left:285px;top:431px">
  <svg class="fold" width="60" height="70"><use href="#fold"/></svg>
  <svg class="icon" width="40" height="40" viewBox="0 0 40 40"><circle cx="20" cy="20" r="19" fill="var(--white)"/><rect x="10" y="11" width="20" height="9" rx="3" fill="var(--pink)"/><rect x="14" y="20" width="12" height="11" rx="2" fill="var(--pink)"/><circle cx="20" cy="25" r="2.5" fill="var(--white)"/></svg>
  <h3><span>Laminating &amp; Binding</span></h3>
  <h4>Laminating and binding</h4>
  <p>Create a professional image for your documents or books. Lamination and binding also keeps your documents well protected!</p>
  <div class="btn">READ MORE <svg width="6" height="8" viewBox="0 0 6 8"><path d="M1 1 L4.5 4 L1 7" stroke="var(--pink)" stroke-width="1.8" fill="none"/></svg></div>
</article>

<article class="abs card" style="left:491px;top:431px">
  <svg class="fold" width="60" height="70"><use href="#fold"/></svg>
  <svg class="icon" width="40" height="40" viewBox="0 0 40 40"><rect x="12" y="3" width="16" height="10" fill="var(--white)"/><rect x="2" y="13" width="36" height="16" rx="2" fill="var(--white)"/><rect x="9" y="24" width="22" height="13" fill="var(--white)" stroke="var(--pink)" stroke-width="1.5"/><line x1="12" y1="29" x2="28" y2="29" stroke="var(--pink)" stroke-width="1.2"/><line x1="12" y1="33" x2="28" y2="33" stroke="var(--pink)" stroke-width="1.2"/></svg>
  <h3><span>Digital Printing</span></h3>
  <h4>All digital format printing</h4>
  <p>Either email us your file or bring it into the store and we can get you the print you need. All prints are to the highest quality.</p>
  <div class="btn">READ MORE <svg width="6" height="8" viewBox="0 0 6 8"><path d="M1 1 L4.5 4 L1 7" stroke="var(--pink)" stroke-width="1.8" fill="none"/></svg></div>
</article>

<article class="abs card" style="left:78px;top:645px">
  <svg class="fold" width="60" height="70"><use href="#fold"/></svg>
  <svg class="icon" width="40" height="40" viewBox="0 0 40 40"><circle cx="20" cy="20" r="18" fill="var(--white)"/><circle cx="20" cy="11" r="4.5" fill="var(--pink)"/><circle cx="20" cy="29" r="4.5" fill="var(--pink)"/><circle cx="11" cy="20" r="4.5" fill="var(--pink)"/><circle cx="29" cy="20" r="4.5" fill="var(--pink)"/><circle cx="20" cy="20" r="2" fill="var(--pink)"/></svg>
  <h3><span>Film Processing</span></h3>
  <h4>Film photo processing</h4>
  <p>Bring in your film to the store and we will work with you to get the best quality print for your purpose and needs. We work with it all!</p>
  <div class="btn">READ MORE <svg width="6" height="8" viewBox="0 0 6 8"><path d="M1 1 L4.5 4 L1 7" stroke="var(--pink)" stroke-width="1.8" fill="none"/></svg></div>
</article>

<article class="abs card" style="left:285px;top:645px">
  <svg class="fold" width="60" height="70"><use href="#fold"/></svg>
  <svg class="icon" width="44" height="40" viewBox="0 0 44 40"><rect x="1" y="6" width="42" height="28" rx="2" fill="var(--white)"/><rect x="5" y="10" width="13" height="14" fill="var(--pink)"/><rect x="22" y="12" width="17" height="2.5" fill="var(--pink)"/><rect x="22" y="18" width="17" height="2.5" fill="var(--pink)"/><rect x="22" y="24" width="17" height="2.5" fill="var(--pink)"/></svg>
  <h3><span>Business Cards</span></h3>
  <h4>Personal desktop publishing</h4>
  <p>From personalised brochures, posters and birth-day and special occasion cards to top quality, cheap business cards - you get it all!</p>
  <div class="btn">READ MORE <svg width="6" height="8" viewBox="0 0 6 8"><path d="M1 1 L4.5 4 L1 7" stroke="var(--pink)" stroke-width="1.8" fill="none"/></svg></div>
</article>

<article class="abs card" style="left:491px;top:645px">
  <svg class="fold" width="60" height="70"><use href="#fold"/></svg>
  <svg class="icon" width="40" height="40" viewBox="0 0 40 40"><rect x="10" y="2" width="20" height="10" rx="1" fill="var(--white)"/><rect x="2" y="13" width="36" height="17" rx="4" fill="var(--white)"/><rect x="9" y="26" width="22" height="11" fill="var(--white)" stroke="var(--pink)" stroke-width="1.5"/><line x1="6" y1="19" x2="34" y2="19" stroke="var(--pink)" stroke-width="1.5"/></svg>
  <h3><span>Photo Printing</span></h3>
  <h4>Quality digital photo prints</h4>
  <p>Get your photo printed to your requirements - either from a file or from your digital camera. With a wide range of options you can get the print you want.</p>
  <div class="btn">READ MORE <svg width="6" height="8" viewBox="0 0 6 8"><path d="M1 1 L4.5 4 L1 7" stroke="var(--pink)" stroke-width="1.8" fill="none"/></svg></div>
</article>

<section class="abs quote">
  <h2 class="abs" style="left:78px;top:28px">Get a free quote</h2>
  <p class="abs quote-text">...or talk to our team about your requirements. Please fill out the form below and we will contact you within a day. You can now upload and send us your file for a free quote</p>
  <h2 class="abs" style="left:78px;top:152px">Follow Us!</h2>
  <div class="abs socials" aria-label="Social links"><div></div><div></div><div></div><div></div><div></div><div></div></div>
  <h2 class="abs" style="left:388px;top:28px">Equire Form</h2>
  <div class="abs field" style="left:388px;top:57px;width:142px;height:22px">First name</div>
  <div class="abs field" style="left:539px;top:57px;width:142px;height:22px">Last name</div>
  <div class="abs field" style="left:388px;top:87px;width:142px;height:22px">Number</div>
  <div class="abs field" style="left:539px;top:87px;width:142px;height:22px">Email</div>
  <div class="abs field" style="left:388px;top:116px;width:293px;height:66px">Message</div>
  <div class="abs submit">SUBMIT</div>
</section>

<footer class="abs footer">Home | About | Photocopying | Printing | Laminating | Business cards | Typing Services | Film Processing | Photo Printing | Passport Photos | Image Restoration | Printer Supplies | Free Quote | Contact</footer>
<div class="abs copyright">© Copyright 2015 Inkvale Printing Shop . All Rights Reserved.</div>
</body>
</html>
```